Natural Light/Organic/Documentary Photography Business

I like a simple, approachable, feminine, earthy/organic feel. Earth/neutral tones, nothing too loud or obnoxious. I like the watercolor look. I don't want anything too trendy or something I'll get tired of after a couple months. As far as colors, I am much more a fan of cream/taupe/blue/green...not a fan of pink or purple at all.

Target Market(s)

Weddings & Families

Industry/Entity Type

Wedding Photography

Contact Information for Business Card

website, email, phone number

Font styles to use
Other font styles liked:
• Horizontes, Gotham

Colors

Designer to choose colors to be used in the design.

Requirements
Must have
• Website: www.mirelhatchway.com
• Phone: 418.629.5073
• Email: mirel@mirelhatchway.com
Nice to have
• I like the watercolor look but its not necessary. I like simple/earthy tones. Nothing too loud or distracting. Simple & feminine without being too girly. I like an approachable/soft feel.
• Instagram: www.instagram.com/mirelhatchwayphotography/
Should not have
• NO loud colors or design or pattern. I do not want a photo of a camera or lens or anything cheesy like that.

```html
<!DOCTYPE html>
<html lang="en">
<head>
<meta charset="utf-8">
<title>Mirel Hatchway Photography – Business Cards</title>
<link rel="stylesheet" href="https://fonts.googleapis.com/css2?family=Allura&family=Montserrat:wght@300;400&display=swap">
<style>
  :root {
    --stage: #1f1f1f;
    --paper: #ffffff;
    --ink-light: #f4f1ec;
    --taupe: #9a8a80;
    --taupe-dark: #7d7069;
    --forest: #3f5a34;
    --forest-deep: #1c2a18;
    --sage: #7f9a6a;
    --peach-soft: #f1cdb5;
    --teal-soft: #8fa7a3;
    --slate-soft: #b4c3c1;
  }
  * { box-sizing: border-box; margin: 0; padding: 0; }
  html, body {
    width: 1200px; height: 1200px; overflow: hidden;
    background: var(--stage);
  }
  .stage {
    width: 1200px; height: 1200px;
    display: flex; flex-direction: column;
    align-items: center; justify-content: center;
    gap: 70px;
  }
  .card {
    position: relative;
    width: 860px; height: 491px;
    overflow: hidden;
    box-shadow: 0 18px 40px rgba(0,0,0,0.5);
  }
  /* Front */
  .card-front .photo-area {
    position: absolute; inset: 0;
    background:
      radial-gradient(ellipse 32% 55% at 52% 42%, rgba(150,110,90,0.7), rgba(150,110,90,0) 70%),
      radial-gradient(ellipse 60% 70% at 40% 40%, var(--sage), rgba(127,154,106,0) 75%),
      linear-gradient(160deg, var(--forest) 0%, #2e4426 55%, var(--forest-deep) 100%);
  }
  .card-front .shade {
    position: absolute; inset: 0;
    background: linear-gradient(180deg, rgba(0,0,0,0) 35%, rgba(0,0,0,0.45) 100%);
  }
  .viewfinder { position: absolute; inset: 0; }
  .front-text {
    position: absolute; left: 0; right: 0; top: 190px;
    text-align: center; color: var(--ink-light);
    font-family: "Montserrat", sans-serif; font-weight: 300;
  }
  .brand-name {
    font-family: "Allura", cursive;
    font-size: 80px; line-height: 1; font-weight: 400;
  }
  .brand-sub {
    font-family: "Montserrat", sans-serif;
    font-size: 12px; letter-spacing: 0.55em; font-weight: 400;
    margin-top: 4px; padding-left: 0.55em;
  }
  .contact { margin-top: 26px; font-size: 19px; line-height: 1.55; letter-spacing: 0.02em; }
  .contact .sep { margin: 0 14px; }
  /* Back */
  .card-back { background: var(--paper); }
  .card-back .border {
    position: absolute; inset: 22px;
    border: 2px solid var(--taupe);
  }
  .card-back .wash-area {
    position: absolute; inset: 40px;
    background:
      radial-gradient(ellipse 45% 40% at 25% 22%, rgba(241,205,181,0.9), rgba(241,205,181,0) 70%),
      radial-gradient(ellipse 40% 45% at 78% 80%, rgba(241,205,181,0.85), rgba(241,205,181,0) 70%),
      radial-gradient(ellipse 50% 45% at 80% 18%, rgba(143,167,163,0.85), rgba(143,167,163,0) 72%),
      radial-gradient(ellipse 50% 45% at 18% 82%, rgba(143,167,163,0.85), rgba(143,167,163,0) 72%),
      linear-gradient(180deg, var(--slate-soft), #e9ddd3 50%, var(--slate-soft));
    opacity: 0.8;
  }
  .name-panel {
    position: absolute; left: 50%; top: 50%;
    width: 500px; height: 196px;
    transform: translate(-50%, -50%);
    background: var(--paper);
    border: 2px solid var(--taupe);
    display: flex; flex-direction: column;
    align-items: center; justify-content: center;
    color: var(--taupe-dark);
  }
  .name-panel .brand-name { font-size: 68px; }
  .name-panel .brand-sub { color: var(--taupe); }
</style>
</head>
<body>
<main class="stage">
  <section class="card card-front">
    <div class="photo-area" role="img" aria-label="Photograph of the photographer among green foliage"></div>
    <div class="shade"></div>
    <svg class="viewfinder" width="860" height="491" viewBox="0 0 860 491" fill="none" stroke="#f4f1ec" stroke-width="3">
      <polyline points="40,90 40,40 90,40"/>
      <polyline points="770,40 820,40 820,90"/>
      <polyline points="40,401 40,451 90,451"/>
      <polyline points="770,451 820,451 820,401"/>
    </svg>
    <div class="front-text">
      <h1 class="brand-name">Mirel Hatchway</h1>
      <p class="brand-sub">PHOTOGRAPHY</p>
      <div class="contact">
        <p class="phone">418.629.5073</p>
        <p><span class="email">mirel@mirelhatchway.com</span><span class="sep">|</span><span class="web">www.mirelhatchway.com</span></p>
        <p class="address">27 Birchwood Road, Maplecrest, QC G1R 4P2</p>
      </div>
    </div>
  </section>

  <section class="card card-back">
    <div class="wash-area" role="img" aria-label="Soft watercolor brush pattern in teal, slate and peach"></div>
    <div class="border"></div>
    <div class="name-panel">
      <h2 class="brand-name">Mirel Hatchway</h2>
      <p class="brand-sub">PHOTOGRAPHY</p>
    </div>
  </section>
</main>
</body>
</html>
```